Nanny Share Ecommerce Website for Finding Childcare and Parents who need Childcare BrightPramHub.net

Our company needs an ecommerce website (BrightPramHub.net) for a US subscription based service strictly for nanny sharing that connects families and caregivers. The website would allow families to connect with one another as well as to search for nannies. The service would be searchable for other families by location (by radius or zip code), children demographic (age range/gender/special needs), days of week or times, after school care, school closure days (holidays), etc. The service would also be searchable for nannies based on gender, provider age range, years experience, language, hourly rate, transportation available, certification (CPR first aid), education etc. The search fields would be searchable and sortable and allow to connect with the provider (after paying subscription fee). The service would be similar to tendlyfolk.net in that it would allow for families and caregivers to post photos as well as a short bio of the themselves. There would also be a feedback/star rating mechanism to rate caregivers who have performed work for families (viewable to public). The service would be free for nannies to post their bios and only a subscription based service for families to connect with other families or with caregivers (able to view bio but need service to connect). There will be a short bio on the benefits of nanny sharing (reduced cost, increased flexibility for parents, reduced illness, increased socialization with other children vs. sole nanny), as well as Q&A section with best practices.

Target Market(s)

Families, Nannies

Industry/Entity Type

Childcare

Logo Text

Bright Pram Hub

Coding

Coded - Design and coding required

Number of Pages Required

5+ page

Requirements
Must have
• Searchable (need to be able to search for families as well as nannies), responsive, functional, easy to use, add value to families and nannies. Needs to be able to collect payment for subscription.
Nice to have
• Optimized for mobile, SEO optimized

```html
<!DOCTYPE html>
<html lang="en">
<head>
<meta charset="utf-8">
<title>Bright Pram Hub – Nanny Sharing</title>
<link rel="stylesheet" href="https://fonts.googleapis.com/css2?family=Open+Sans:wght@400;600;700&family=Roboto+Condensed:wght@400;700&display=swap">
<style>
:root{
  --green:#3f9c7c;
  --green-dark:#2f8466;
  --blue:#1b6fc0;
  --blue-deep:#0c4ea3;
  --nav-top:#4aa0dc;
  --nav-bottom:#1f78c1;
  --ink:#222;
  --muted:#555;
  --line:#d6d6d6;
  --soft:#f2f2f2;
  --footer:#0b0b0b;
  --star:#f39a1c;
  --white:#fff;
}
*{box-sizing:border-box;margin:0;padding:0}
html,body{width:1200px;height:3333px;overflow:hidden}
body{position:relative;background:var(--white);font-family:"Open Sans",Arial,sans-serif;color:var(--ink)}
.abs{position:absolute}

/* Header */
.site-header{position:absolute;left:0;top:0;width:1200px;height:129px;background:var(--white)}
.brand{position:absolute;left:89px;top:26px;display:flex;align-items:center;gap:14px}
.brand-mark{width:80px;height:80px;border-radius:50%;background:var(--green)}
.brand-name{font-family:"Open Sans",Arial,sans-serif;font-weight:700;font-size:27px;line-height:31px;color:#1e2a2a}
.contact-item{position:absolute;top:36px;display:flex;align-items:center;gap:14px}
.contact-icon{width:48px;height:48px;border-radius:50%;border:2px solid #cfd8e3;display:flex;align-items:center;justify-content:center}
.contact-label{font-size:15px;color:var(--blue);line-height:20px}
.contact-value{font-size:15px;color:#666;line-height:22px}
.login-btn{position:absolute;left:1007px;top:44px;width:100px;height:36px;border-radius:8px;background:var(--green);color:var(--white);font-size:17px;display:flex;align-items:center;justify-content:center}

/* Nav */
.main-nav{position:absolute;left:0;top:129px;width:1200px;height:60px;background:linear-gradient(var(--nav-top),var(--nav-bottom))}
.main-nav a{position:absolute;top:0;height:60px;line-height:60px;color:var(--white);font-size:17px;text-decoration:none;transform:translateX(-50%)}
.main-nav a.is-active{left:89px;width:115px;transform:none;text-align:center;background:var(--green)}

/* Hero */
.hero{position:absolute;left:0;top:189px;width:1200px;height:600px;overflow:hidden}
.hero-photo{position:absolute;inset:0;background:linear-gradient(100deg,#8a8b7f 0%,#b6b2a0 25%,#d9c97a 45%,#c9b24e 60%,#8d9a62 80%,#5f7447 100%)}
.hero-card{position:absolute;left:89px;top:193px;width:367px;height:185px;background:var(--white);padding:14px 0 0 46px}
.hero-title{font-family:"Roboto Condensed",Arial,sans-serif;font-size:42px;color:var(--blue);line-height:50px}
.hero-sub{font-family:"Roboto Condensed",Arial,sans-serif;font-size:23px;color:#222;line-height:32px}
.hero-btn{position:absolute;top:122px;height:43px;border-radius:22px;color:var(--white);font-size:20px;display:flex;align-items:center;justify-content:center}
.hero-btn.care{left:29px;width:144px;background:var(--green)}
.hero-btn.nanny{left:184px;width:145px;background:var(--blue)}
.hero-dots{position:absolute;left:94px;top:412px;color:#fff;font-size:16px;letter-spacing:10px}
.hero-curve{position:absolute;left:0;bottom:0;width:1200px;height:100px}

/* Welcome */
.welcome-title{position:absolute;left:0;top:876px;width:1200px;text-align:center;font-family:"Roboto Condensed",Arial,sans-serif;font-size:37px;color:#1d1d1d}
.welcome-text{position:absolute;left:186px;top:936px;width:832px;text-align:center;font-size:13.5px;line-height:24px;color:var(--muted)}

/* Services */
.service{position:absolute;top:1089px;width:220px;text-align:center;transform:translateX(-50%)}
.service-photo{width:140px;height:140px;border-radius:50%;margin:0 auto;border:3px solid #e6e6e6}
.service-name{margin-top:24px;font-size:18px;color:#333}
.service-more{margin-top:6px;font-size:13px;color:var(--blue)}
.slider-arrow{position:absolute}

/* Benefits */
.benefits{position:absolute;left:0;top:1391px;width:1200px;height:453px;overflow:hidden}
.benefits-photo{position:absolute;inset:0;background:linear-gradient(120deg,#cfd7e0 0%,#e9dfd2 40%,#c8a47d 70%,#9fb6c9 100%)}
.benefits-panel{position:absolute;inset:0}
.benefits-title{position:absolute;left:89px;top:70px;font-family:"Roboto Condensed",Arial,sans-serif;font-size:34px;color:var(--white)}
.benefits-lead{position:absolute;left:89px;top:120px;width:540px;font-size:18px;line-height:27px;color:var(--white)}
.benefits-text{position:absolute;left:89px;top:186px;width:527px;font-size:15px;line-height:25px;color:#eef3fb;text-align:justify}
.benefits-btn{position:absolute;left:89px;top:324px;width:120px;height:43px;border:1px solid #cfe0f5;border-radius:4px;color:var(--white);font-size:15px;display:flex;align-items:center;justify-content:center;gap:6px}

/* FAQ */
.faq-title{position:absolute;left:0;top:1926px;width:1200px;text-align:center;font-family:"Roboto Condensed",Arial,sans-serif;font-size:36px;color:#1d1d1d}
.faq-item{position:absolute;left:171px;width:858px;height:89px;background:var(--white);border-left:7px solid var(--green);box-shadow:0 2px 6px rgba(0,0,0,.22);padding:17px 0 0 30px}
.faq-q{font-size:18px;color:#222;line-height:26px}
.faq-a{font-size:14px;color:#444;line-height:24px;margin-top:4px}

/* Reviews */
.reviews{position:absolute;left:0;top:2507px;width:1200px;height:431px;background:var(--soft)}
.reviews-title{position:absolute;left:0;top:49px;width:1200px;text-align:center;font-family:"Roboto Condensed",Arial,sans-serif;font-size:36px;color:#1d1d1d}
.review-quote{position:absolute;left:190px;top:124px;width:820px;text-align:center;font-size:14px;line-height:25px;color:#444}
.quote-mark{font-family:Georgia,serif;font-size:34px;color:var(--blue);font-weight:700;line-height:0;vertical-align:-10px}
.review-avatar{position:absolute;left:564px;top:221px;width:90px;height:90px;border-radius:50%;background:linear-gradient(#e2c2a5,#b98662);border:3px solid var(--white)}
.review-name{position:absolute;left:0;top:322px;width:1200px;text-align:center;font-style:italic;font-size:14px;color:#333}
.review-stars{position:absolute;left:554px;top:360px;display:flex;gap:4px}

/* Footer */
.site-footer{position:absolute;left:0;top:2938px;width:1200px;height:395px;background:var(--footer);color:var(--white)}
.newsletter-label{position:absolute;left:278px;top:55px;font-family:"Roboto Condensed",Arial,sans-serif;font-size:27px;letter-spacing:.5px}
.newsletter-input{position:absolute;left:469px;top:51px;width:350px;height:40px;border-radius:20px 0 0 20px;background:var(--white);color:#aaa;font-size:12px;padding-left:22px;line-height:40px}
.newsletter-btn{position:absolute;left:816px;top:51px;width:93px;height:40px;border-radius:0 20px 20px 0;background:var(--green);font-size:12px;display:flex;align-items:center;justify-content:center}
.footer-rule{position:absolute;left:96px;width:1008px;height:1px;background:#333}
.footer-col{position:absolute;top:172px}
.footer-head{font-size:14px;letter-spacing:.3px}
.footer-list{list-style:none;margin-top:10px}
.footer-list li{font-size:11.5px;line-height:24.5px;color:#e8e8e8}
.footer-list.links li::before{content:"» ";}
.social{position:absolute;left:936px;top:172px}
.social-row{display:flex;gap:11px;margin-top:16px}
.social-dot{width:29px;height:29px;border-radius:50%;background:var(--white)}
.copyright{position:absolute;left:0;top:356px;width:1200px;text-align:center;font-size:11px;color:#ddd}
</style>
</head>
<body>

<header class="site-header">
  <div class="brand">
    <div class="brand-mark"></div>
    <div class="brand-name">Bright Pram<br>Hub</div>
  </div>
  <div class="contact-item" style="left:527px">
    <div class="contact-icon">
      <svg width="24" height="18" viewBox="0 0 24 18"><rect x="1" y="1" width="22" height="16" rx="2" fill="none" stroke="#2f6fb3" stroke-width="2"/><path d="M2 2l10 8 10-8" fill="none" stroke="#2f6fb3" stroke-width="2"/></svg>
    </div>
    <div><div class="contact-label">Email id</div><div class="contact-value">hello@brightpramhub.net</div></div>
  </div>
  <div class="contact-item" style="left:796px">
    <div class="contact-icon">
      <svg width="22" height="22" viewBox="0 0 24 24"><path d="M6.6 10.8a15 15 0 006.6 6.6l2.2-2.2a1 1 0 011-.25 11.4 11.4 0 003.6.57 1 1 0 011 1V20a1 1 0 01-1 1A17 17 0 013 4a1 1 0 011-1h3.5a1 1 0 011 1c0 1.25.2 2.45.57 3.57a1 1 0 01-.25 1z" fill="#2f6fb3"/></svg>
    </div>
    <div><div class="contact-label">Phone</div><div class="contact-value">415.306.2274</div></div>
  </div>
  <div class="login-btn">LOGIN</div>
</header>

<nav class="main-nav">
  <a class="is-active">Home</a>
  <a style="left:298px">About Us</a>
  <a style="left:460px">Services</a>
  <a style="left:618px">Benefits</a>
  <a style="left:749px">FAQ</a>
  <a style="left:893px">Join Now</a>
  <a style="left:1064px">Contact Us</a>
</nav>

<section class="hero">
  <div class="hero-photo" role="img" aria-label="Photo of a mother in a sun hat holding her smiling toddler outdoors"></div>
  <div class="hero-card">
    <div class="hero-title">Bright Pram Hub</div>
    <div class="hero-sub">Neque porro quisquam est</div>
    <div class="hero-btn care">Find Care</div>
    <div class="hero-btn nanny">Find Nanny</div>
  </div>
  <div class="hero-dots">‹ ›</div>
  <svg class="hero-curve" viewBox="0 0 1200 100" preserveAspectRatio="none">
    <path d="M0 40 Q600 115 1200 40 L1200 100 L0 100Z" fill="#a9a9a9"/>
    <path d="M0 55 Q600 128 1200 55 L1200 100 L0 100Z" fill="#ffffff"/>
  </svg>
</section>

<h1 class="welcome-title">Welcome to Bright Pram Hub</h1>
<p class="welcome-text">It is a long established fact that a reader will be distracted by the readable content of a page when looking at its layout. The point of using Lorem Ipsum is that it has a more-or-less normal distribution of letters, as opposed to using 'Content here, content here', making it look like readable English. Many desktop publishing packages and web page editors</p>

<svg class="slider-arrow" style="left:44px;top:1202px" width="22" height="38" viewBox="0 0 22 38"><path d="M20 2L3 19l17 17" fill="none" stroke="#999" stroke-width="2"/></svg>
<svg class="slider-arrow" style="left:1134px;top:1202px" width="22" height="38" viewBox="0 0 22 38"><path d="M2 2l17 17L2 36" fill="none" stroke="#999" stroke-width="2"/></svg>

<div class="service" style="left:204px">
  <div class="service-photo" role="img" aria-label="Photo of a young child playing with toy blocks" style="background:linear-gradient(#f1d7b8,#e6a35c)"></div>
  <div class="service-name">Child care</div>
  <div class="service-more">Read More -&gt;</div>
</div>
<div class="service" style="left:471px">
  <div class="service-photo" role="img" aria-label="Photo of a caregiver with an elderly woman" style="background:linear-gradient(#f2ece6,#c9a68d)"></div>
  <div class="service-name">Adult and senior care</div>
  <div class="service-more">Read More -&gt;</div>
</div>
<div class="service" style="left:722px">
  <div class="service-photo" role="img" aria-label="Photo of a man with his dog" style="background:linear-gradient(#e9b575,#a8744a)"></div>
  <div class="service-name">Pet care</div>
  <div class="service-more">Read More -&gt;</div>
</div>
<div class="service" style="left:980px">
  <div class="service-photo" role="img" aria-label="Photo of a smiling home care worker" style="background:linear-gradient(#f4f1ee,#8a6a55)"></div>
  <div class="service-name">Home care</div>
  <div class="service-more">Read More -&gt;</div>
</div>

<section class="benefits">
  <div class="benefits-photo" role="img" aria-label="Photo of a caregiver laughing with a girl at a craft table"></div>
  <svg class="benefits-panel" viewBox="0 0 1200 453" preserveAspectRatio="none">
    <defs><linearGradient id="benefitsBlue" x1="0" y1="0" x2="1" y2="1"><stop offset="0" stop-color="#1262b8"/><stop offset="1" stop-color="#0b4598"/></linearGradient></defs>
    <path d="M0 0H773L644 453H0Z" fill="url(#benefitsBlue)"/>
  </svg>
  <h2 class="benefits-title">Benefits</h2>
  <p class="benefits-lead">Reduced cost, increased flexibility for parents, reduced illness, increased socialization with other children vs. sole nanny</p>
  <p class="benefits-text">It is a long established fact that a reader will be distracted by the readable content of a page when looking at its layout. The point of using Lorem Ipsum is that it has a more-or-less normal distribution of letters, as opposed to using 'Content here, content here', making it look like readable English. Many desktop publishing packages</p>
  <div class="benefits-btn">Read More <svg width="9" height="10" viewBox="0 0 9 10"><path d="M1 1l4 4-4 4M4 1l4 4-4 4" fill="none" stroke="#fff" stroke-width="1.4"/></svg></div>
</section>

<h2 class="faq-title">FAQ</h2>
<div class="faq-item" style="top:2011px">
  <div class="faq-q">Q- Neque porro quisquam est qui dolorem ipsum ?</div>
  <div class="faq-a">A- It is a long established fact that a reader will be distracted by the readable content of a page .</div>
</div>
<div class="faq-item" style="top:2114px">
  <div class="faq-q">Q- quisquam est qui dolorem ipsum quia dolor sit amet?</div>
  <div class="faq-a">A- The point of using Lorem Ipsum is that it has a more-or-less normal distribution of letters, as opposed</div>
</div>
<div class="faq-item" style="top:2217px">
  <div class="faq-q">Q- Neque porro quisquam est qui dolorem ipsum quia dolor sit amet?</div>
  <div class="faq-a">A- Lorem Ipsum as their default model text, and a search for 'lorem ipsum' will uncover many web sites.</div>
</div>
<div class="faq-item" style="top:2320px">
  <div class="faq-q">Q- Porro quisquam est qui dolorem ipsum quia dolor sit amet, consectetur?</div>
  <div class="faq-a">A- Various versions have evolved over the years, sometimes by accident, sometimes on purpose</div>
</div>

<section class="reviews">
  <h2 class="reviews-title">Reviews</h2>
  <p class="review-quote"><span class="quote-mark">“</span> It has survived not only five centuries, but also the leap into electronic typesetting, remaining essentially unchanged. It was popularised in the 1960s with the release of Typeleaf sheets containing Lorem Ipsum passages, and more recently with desktop publishing software like Quillset LayoutPro including versions of Lorem Ipsum <span class="quote-mark">”</span></p>
  <svg class="abs" style="left:518px;top:254px" width="16" height="26" viewBox="0 0 16 26"><path d="M14 2L3 13l11 11" fill="none" stroke="#888" stroke-width="2.5"/></svg>
  <div class="review-avatar" role="img" aria-label="Portrait of the reviewer"></div>
  <svg class="abs" style="left:682px;top:254px" width="16" height="26" viewBox="0 0 16 26"><path d="M2 2l11 11L2 24" fill="none" stroke="#888" stroke-width="2.5"/></svg>
  <div class="review-name">Neque porro quisquam</div>
  <div class="review-stars">
    <svg width="18" height="18" viewBox="0 0 24 24"><path d="M12 2l3 6.6 7.2.8-5.4 4.9 1.5 7.1L12 17.8 5.7 21.4l1.5-7.1L1.8 9.4 9 8.6z" fill="var(--star)"/></svg>
    <svg width="18" height="18" viewBox="0 0 24 24"><path d="M12 2l3 6.6 7.2.8-5.4 4.9 1.5 7.1L12 17.8 5.7 21.4l1.5-7.1L1.8 9.4 9 8.6z" fill="var(--star)"/></svg>
    <svg width="18" height="18" viewBox="0 0 24 24"><path d="M12 2l3 6.6 7.2.8-5.4 4.9 1.5 7.1L12 17.8 5.7 21.4l1.5-7.1L1.8 9.4 9 8.6z" fill="var(--star)"/></svg>
    <svg width="18" height="18" viewBox="0 0 24 24"><path d="M12 2l3 6.6 7.2.8-5.4 4.9 1.5 7.1L12 17.8 5.7 21.4l1.5-7.1L1.8 9.4 9 8.6z" fill="var(--star)"/></svg>
    <svg width="18" height="18" viewBox="0 0 24 24"><path d="M12 2l3 6.6 7.2.8-5.4 4.9 1.5 7.1L12 17.8 5.7 21.4l1.5-7.1L1.8 9.4 9 8.6z" fill="var(--star)"/></svg>
  </div>
</section>

<footer class="site-footer">
  <div class="newsletter-label">NEWSLETTER</div>
  <div class="newsletter-input">email@example.com</div>
  <div class="newsletter-btn">SUBSCRIBE</div>
  <div class="footer-rule" style="top:135px"></div>

  <div class="footer-col" style="left:96px">
    <div class="footer-head">INFORMATION</div>
    <ul class="footer-list links"><li>Privacy Policy</li><li>FAQ</li><li>Sitemap</li><li>Contact Us</li></ul>
  </div>
  <div class="footer-col" style="left:371px">
    <div class="footer-head">LINKS</div>
    <ul class="footer-list links"><li>Home</li><li>Services</li><li>Benefits</li><li>About us</li></ul>
  </div>
  <div class="footer-col" style="left:613px">
    <div class="footer-head">CONTACT US</div>
    <ul class="footer-list"><li>Address : Willowmere Lane 18 5120 KD</li><li>&nbsp;&nbsp;Ambervale Westland</li><li>Phone : +31 (0)172-508300</li><li>Email : hello@brightpramhub.net</li></ul>
  </div>
  <div class="social">
    <div class="footer-head">FOLLOW US OUT THERE</div>
    <div class="social-row"><div class="social-dot"></div><div class="social-dot"></div><div class="social-dot"></div></div>
  </div>

  <div class="footer-rule" style="top:328px"></div>
  <div class="copyright">Copyright © 2018. All Rights Reserved</div>
</footer>

</body>
</html>
```